Veltrane Group Business Card Design

The CEO is looking for a new trendy look for his business card.
You can stay with current branding or come up with something new/creative. It can be 3D, including Medical Office buildings. You can use our logo in a variety of colors. Please include name, title, company name, company website, email address, cell number

Target Market(s)

Real Estate Development and Construction

Industry/Entity Type

Health care real estate

Contact Information for Business Card

Rohesh Kamdar, CEO M-604.781.2249 E-roheshkamdar@veltrane.com Address:4180 Lindqvist Ave, Harlow Point, OR 97482 www.veltrane.com

Font styles to use
Other font styles liked:
• Be creative

Requirements
Must have
• Creative, trendy look
Nice to have
• Please go to our website to get a feel- www. veltrane.com
Should not have
• small fonts

```html
<!DOCTYPE html>
<html lang="en">
<head>
<meta charset="utf-8">
<title>Veltrane Group Business Card</title>
<link href="https://fonts.googleapis.com/css2?family=Lato:wght@400;700;900&display=swap" rel="stylesheet">
<style>
  :root {
    --bg: #c9c9c9;
    --paper: #ffffff;
    --ink: #111111;
    --ink-soft: #333333;
    --band: #0d0d0d;
    --back-dark: #151515;
    --back-mid: #2a2a2a;
    --rule: #555555;
  }
  * { margin: 0; padding: 0; box-sizing: border-box; }
  html, body { width: 1200px; height: 788px; overflow: hidden; }
  body {
    background: var(--bg);
    font-family: "Lato", sans-serif;
    position: relative;
  }
  .card {
    position: absolute;
    width: 600px;
    height: 343px;
    border-radius: 22px;
    overflow: hidden;
  }
  .card-front {
    left: 70px; top: 90px;
    background: var(--paper);
    z-index: 2;
    box-shadow: 0 6px 18px rgba(0,0,0,0.25);
  }
  .card-back {
    left: 530px; top: 355px;
    z-index: 1;
    box-shadow: 0 6px 18px rgba(0,0,0,0.25);
  }
  .brand-name {
    position: absolute;
    left: 150px; top: 48px;
    font-weight: 900;
    font-size: 58px;
    line-height: 1;
    letter-spacing: -1.5px;
    color: var(--ink);
  }
  .brand-name .brand-sub {
    display: block;
    text-align: right;
    font-size: 30px;
    letter-spacing: 0;
    margin-top: 2px;
  }
  .person {
    position: absolute;
    left: 60px; top: 178px;
    width: 210px;
    text-align: right;
  }
  .person-name {
    font-weight: 700;
    font-size: 25px;
    color: var(--ink);
  }
  .person-title {
    font-size: 15px;
    color: var(--ink-soft);
    letter-spacing: 1px;
    margin-top: 4px;
  }
  .divider {
    position: absolute;
    left: 290px; top: 170px;
    width: 1px; height: 78px;
    background: var(--rule);
  }
  .contacts {
    position: absolute;
    left: 308px; top: 166px;
    list-style: none;
  }
  .contacts li {
    display: flex;
    align-items: center;
    gap: 10px;
    font-size: 16px;
    color: var(--ink-soft);
    height: 28px;
  }
  .contacts svg { width: 15px; height: 15px; flex: none; }
  .address-band {
    position: absolute;
    left: 0; right: 0; top: 268px;
    height: 42px;
    background: var(--band);
    color: var(--paper);
    display: flex;
    align-items: center;
    padding-left: 82px;
    gap: 10px;
    font-size: 17px;
    letter-spacing: 0.3px;
  }
  .address-band svg { width: 14px; height: 18px; }
  .back-pattern {
    position: absolute; inset: 0;
    background: linear-gradient(135deg, var(--back-dark) 0%, var(--back-mid) 100%);
  }
  .back-name {
    position: absolute;
    left: 0; right: 0; top: 150px;
    text-align: center;
    font-weight: 900;
    font-size: 34px;
    letter-spacing: -0.5px;
    color: var(--paper);
  }
</style>
</head>
<body>
  <section class="card card-front" aria-label="Card front">
    <div class="brand-name">Veltrane<span class="brand-sub">Group</span></div>

    <div class="person">
      <div class="person-name">Rohesh Kamdar</div>
      <div class="person-title">CEO</div>
    </div>

    <div class="divider"></div>

    <ul class="contacts">
      <li>
        <svg viewBox="0 0 16 16" aria-hidden="true"><rect x="4" y="1" width="8" height="14" rx="1.5" fill="none" stroke="#111" stroke-width="1.4"/><circle cx="8" cy="12.5" r="0.8" fill="#111"/></svg>
        604.781.2249
      </li>
      <li>
        <svg viewBox="0 0 16 16" aria-hidden="true"><rect x="1" y="3" width="14" height="10" fill="#111"/><path d="M1 3 L8 9 L15 3" fill="none" stroke="#fff" stroke-width="1.2"/></svg>
        roheshkamdar@veltrane.com
      </li>
      <li>
        <svg viewBox="0 0 16 16" aria-hidden="true"><circle cx="8" cy="8" r="7" fill="#111"/><ellipse cx="8" cy="8" rx="3" ry="7" fill="none" stroke="#fff" stroke-width="1"/><line x1="1" y1="8" x2="15" y2="8" stroke="#fff" stroke-width="1"/></svg>
        www.veltrane.com
      </li>
    </ul>

    <div class="address-band">
      <svg viewBox="0 0 14 18" aria-hidden="true"><path d="M7 0 C3 0 0 3 0 7 C0 12 7 18 7 18 C7 18 14 12 14 7 C14 3 11 0 7 0 Z" fill="#fff"/><circle cx="7" cy="7" r="2.5" fill="#0d0d0d"/></svg>
      4180 Lindqvist Ave, Harlow Point, OR 97482
    </div>
  </section>

  <section class="card card-back" aria-label="Card back">
    <div class="back-pattern" role="img" aria-label="Dark background with repeating brand name texture"></div>
    <div class="back-name">Veltrane</div>
  </section>
</body>
</html>
```